Redesign for existing homepage

We would like a redesign for our websites 2 column homepage
We provide engine repair and reconditioning services
We would like a cleaner, modern site that works well with our logo colors
Please see the attached brief for more info
Target Market(s)
25 - 45
Industry/Entity Type
Cleaner
Requirements
Must have
- Google Fonts

```html
<!DOCTYPE html>
<html lang="en">
<head>
<meta charset="utf-8">
<title>Marlow Engine Works — Home</title>
<link href="https://fonts.googleapis.com/css2?family=Ubuntu:wght@400;500&family=Quicksand:wght@500;600&family=Open+Sans:ital,wght@0,400;1,400&display=swap" rel="stylesheet">
<style>
:root{
  --black:#121212;
  --blue:#0a5fe8;
  --blue-dark:#0b4fc7;
  --link-blue:#1c55c9;
  --yellow:#ffb400;
  --yellow-light:#ffd21f;
  --grey-text:#8a8a8a;
  --dark-text:#333;
  --line:#dcdcdc;
  --band:#ececec;
  --footer-bg:#f6f6f6;
}
*{box-sizing:border-box;margin:0;padding:0}
html,body{width:1083px;height:1200px;overflow:hidden;background:#fff}
body{position:relative;font-family:'Open Sans',sans-serif;color:var(--grey-text)}
.abs{position:absolute}

.site-header{left:0;top:0;width:1083px;height:150px;background:var(--black)}
.brand{left:442px;top:34px;display:flex;align-items:center;gap:10px;font-family:'Ubuntu',sans-serif;font-weight:500;font-size:24px;color:var(--yellow-light);white-space:nowrap}
.brand-dot{width:22px;height:22px;border-radius:50%;background:var(--blue)}
.phone{right:141px;top:48px;text-align:right;font-family:'Ubuntu',sans-serif;color:var(--yellow)}
.phone-label{font-size:14px;line-height:16px}
.phone-number{font-size:25px;line-height:28px}

.main-nav{left:142px;top:104px;width:804px;height:46px;background:linear-gradient(var(--blue),var(--blue-dark));display:flex}
.main-nav a{font-family:'Ubuntu',sans-serif;font-weight:500;font-size:13px;color:#fff;text-decoration:none;display:flex;align-items:center;justify-content:center;border-right:1px solid rgba(255,255,255,.25)}
.main-nav a:last-child{border-right:none}

.hero-band{left:0;top:150px;width:1083px;height:331px;background:var(--band)}
.hero-photo{left:143px;top:150px;width:804px;height:331px;background:linear-gradient(100deg,#b9c6d4 0%,#dfe4ea 35%,#8e98a3 60%,#2b2e33 85%,#1b1c1f 100%)}
.hero-caption{left:143px;top:314px;width:380px;height:82px;background:rgba(40,60,140,.82);clip-path:polygon(0 0,100% 0,94% 100%,0 100%);padding:16px 0 0 22px}
.hero-title{font-family:'Ubuntu',sans-serif;font-weight:500;font-size:24px;color:var(--yellow);line-height:28px}
.hero-sub{font-family:'Ubuntu',sans-serif;font-weight:500;font-size:12.5px;color:#fff;margin-top:4px}
.slider-dots{left:517px;top:460px;display:flex;gap:3px}
.slider-dots span{width:12px;height:12px;border-radius:50%;background:#fff}

.feature{width:180px;text-align:center}
.feature svg{display:block;margin:0 auto}
.feature-title{font-family:'Quicksand',sans-serif;font-weight:500;font-size:14px;line-height:20px;color:var(--link-blue);margin-top:16px}
.feature-text{font-size:10px;line-height:17px;margin-top:5px}
.btn{display:inline-block;margin-top:8px;width:72px;height:21px;line-height:21px;border-radius:2px;background:linear-gradient(var(--yellow-light),var(--yellow));color:#fff;font-size:7.5px;letter-spacing:.2px}

.welcome{left:148px;top:728px;width:540px}
.welcome h1{font-family:'Quicksand',sans-serif;font-weight:500;font-size:23.5px;color:#222;margin-bottom:8px}
.welcome p{font-size:10.2px;line-height:19.3px;padding-left:2px;margin-bottom:4px;white-space:nowrap}

.section-title{font-family:'Quicksand',sans-serif;font-weight:500;color:var(--link-blue)}
.posts-title{left:148px;top:900px;font-size:20px}
.post{width:160px;font-size:10px;line-height:19.3px;top:938px}
.post h3{font-family:'Quicksand',sans-serif;font-weight:500;font-size:12.5px;color:var(--link-blue);margin-bottom:2px}
.post-date{margin-top:2px}

.sidebar-rule{left:705px;top:502px;width:1px;height:575px;background:linear-gradient(var(--line),rgba(220,220,220,0))}
.side-photo{left:730px;width:216px;height:86px}
.side-title{left:730px;font-family:'Quicksand',sans-serif;font-weight:600;font-size:14.5px;color:var(--yellow)}
.side-text{left:730px;font-size:9.5px;white-space:nowrap}
.quote-title{left:732px;top:853px;font-size:19px}
.quote{left:734px;top:886px;font-style:italic;font-size:9.8px;line-height:19.3px;white-space:nowrap}
.quote-author{left:734px;top:1004px;font-size:12px;color:var(--dark-text)}

.site-footer{left:0;top:1095px;width:1083px;height:105px;background:var(--footer-bg);border-top:1px solid var(--line)}
.footer-nav{left:146px;top:1126px;font-size:11.8px;color:#555;white-space:nowrap}
.footer-nav .sep{margin:0 5px;color:#888}
.copyright{left:147px;top:1155px;font-size:10px;color:#888}
.social{left:873px;top:1125px;display:flex;gap:7px}
.social span{width:20px;height:20px;border-radius:2px}
</style>
</head>
<body>

<header class="site-header abs"></header>
<div class="brand abs"><span class="brand-dot"></span>Marlow Engine Works</div>
<div class="phone abs">
  <div class="phone-label">Phone number</div>
  <div class="phone-number">04 555 0192</div>
</div>
<nav class="main-nav abs">
  <a href="#" style="width:67px">Home</a>
  <a href="#" style="width:76px">About Us</a>
  <a href="#" style="width:210px">Private Vehicle Service &amp; Repair</a>
  <a href="#" style="width:124px">Trade Customers</a>
  <a href="#" style="width:179px">Race &amp; Classic Car Engines</a>
  <a href="#" style="width:64px">Enquiry</a>
  <a href="#" style="width:84px">Contact</a>
</nav>

<div class="hero-band abs"></div>
<div class="hero-photo abs" role="img" aria-label="Mechanics working on an open car engine bay"></div>
<div class="hero-caption abs">
  <div class="hero-title">CAR REPAIRING &amp; ENGINES</div>
  <div class="hero-sub">PHASELLUS FELIS DOLOR SCELERISQUE</div>
</div>
<div class="slider-dots abs"><span></span><span></span><span></span><span></span></div>

<section class="feature abs" style="left:138px;top:510px">
  <svg width="50" height="50" viewBox="0 0 50 50" fill="var(--blue)">
    <path d="M6 4 L10 0 L24 14 L40 30 L46 28 L50 40 L44 44 L38 48 L30 44 L32 38 L16 22 L2 8 Z"/>
    <path d="M44 2 L48 6 L40 14 L36 18 L14 40 L12 48 L2 48 L2 38 L10 36 L32 14 L36 10 Z"/>
  </svg>
  <div class="feature-title">Need service and repair<br>for a private vehicle?</div>
  <div class="feature-text">Vivamus porttitor purus<br>nisi eleifend libero</div>
  <a class="btn">CLICK HERE</a>
</section>

<section class="feature abs" style="left:336px;top:510px">
  <svg width="50" height="52" viewBox="0 0 50 52" fill="var(--blue)">
    <circle cx="25" cy="15" r="13"/>
    <path d="M2 52 L2 42 Q2 32 14 30 L25 40 L36 30 Q48 32 48 42 L48 52 Z"/>
  </svg>
  <div class="feature-title">Interested in becoming<br>a trade customer?</div>
  <div class="feature-text">Vivamus porttitor purus<br>nisi eleifend libero</div>
  <a class="btn">CLICK HERE</a>
</section>

<section class="feature abs" style="left:521px;top:516px">
  <svg width="54" height="46" viewBox="0 0 54 46" fill="var(--blue)">
    <path d="M12 4 Q14 0 20 0 L34 0 Q40 0 42 4 L46 14 L52 14 L52 18 L48 18 Q52 22 52 28 L52 42 L44 42 L44 38 L10 38 L10 42 L2 42 L2 28 Q2 22 6 18 L2 18 L2 14 L8 14 Z M14 6 L10 16 L44 16 L40 6 Z"/>
    <circle cx="12" cy="27" r="4" fill="#fff"/><circle cx="42" cy="27" r="4" fill="#fff"/>
  </svg>
  <div class="feature-title" style="margin-top:10px">Is your classic or race<br>car your passion?</div>
  <div class="feature-text">Vivamus porttitor purus<br>nisi eleifend</div>
  <a class="btn">CLICK HERE</a>
</section>

<section class="welcome abs">
  <h1>Welcome to Our Website Mainpage</h1>
  <p>Phasellus felis dolor scelerisque a tempus eget lobortis id libero Donec scelerisque leo ac risus Praesent sit<br>amet est In dictum dolor eu dictum porttitor enim felis viverra mi eget luctus massa purus quis odio Etiam<br>nulla massa pharetra facilisis volutpat in imperdiet sit amet sem</p>
  <p>Aliquam nec erat at purus cursus interdum Vestibulum ligula augue bibendum accumsan vestibulum ut<br>commodo a mi Morbi ornare gravida elit Integer congue augue et malesuada iaculis ipsum</p>
</section>

<h2 class="section-title posts-title abs">Latest Posts</h2>
<article class="post abs" style="left:148px">
  <h3>Aue bibendum</h3>
  <p>accumsan vestibulum ut<br>commodo a mi Morbi ornare<br>gravida elit Integer</p>
  <p class="post-date">20 April 2014</p>
</article>
<article class="post abs" style="left:325px">
  <h3>Felis viverra eget</h3>
  <p>accumsan vestibulum ut<br>commodo a mi Morbi ornare<br>gravida elit Integer</p>
  <p class="post-date">20 April 2014</p>
</article>
<article class="post abs" style="left:493px">
  <h3>Morbi diam mauris</h3>
  <p>accumsan vestibulum ut<br>commodo a mi Morbi ornare<br>gravida elit Integer</p>
  <p class="post-date">20 April 2014</p>
</article>

<div class="sidebar-rule abs"></div>
<div class="side-photo abs" style="top:519px;background:linear-gradient(120deg,#3a3d42,#8a8f96 55%,#d8c8bc)" role="img" aria-label="Hands repairing a vehicle engine"></div>
<div class="side-title abs" style="top:613px">Vehicle Repairing</div>
<div class="side-text abs" style="top:637px">Acumsan vestibulum ut commodo a mi Mor</div>
<div class="side-photo abs" style="top:682px;background:linear-gradient(120deg,#2a2c30,#6d727a 50%,#3b3e43)" role="img" aria-label="Close view of a race car engine"></div>
<div class="side-title abs" style="top:776px">Race &amp; Classic Car Engine</div>
<div class="side-text abs" style="top:800px">Acumsan vestibulum ut commodo Morbornare</div>

<h2 class="section-title quote-title abs">What Our Customer Say</h2>
<p class="quote abs">Mauris vel lacus vitae felis vestibulum volut-<br>pat Etiam est nunc venenatis in tristique eu<br>imperdiet ac nisl Cum sociis natoque penati-<br>bus et magnis dis parturient montes nascetur<br>ridiculus mus In iaculis facilisis massa Etiam<br>eu urna Sed porta Suspendisse</p>
<p class="quote-author abs">By Author Name</p>

<footer class="site-footer abs"></footer>
<div class="footer-nav abs">Home<span class="sep">/</span>About Us<span class="sep">/</span>Private Vehicle Service &amp; Repair<span class="sep">/</span>Trade Customers<span class="sep">/</span>Race &amp; Classic Car Engines<span class="sep">/</span>Enquiry<span class="sep">/</span>Contact</div>
<div class="copyright abs">© 2014 Company Name&nbsp; All right reserved&nbsp; Term of Use</div>
<div class="social abs">
  <span style="background:#3b5b9a"></span>
  <span style="background:#3fb3e6"></span>
  <span style="background:#1f6fb0"></span>
</div>

</body>
</html>
```